Cover for Lanterns Along the Quiet Shore of Being

Cover for a book that describes everything that happens to a person, from pre-birth life plans through growing in compassion and wisdom to death and living in the afterlife. The information is revealed in messages from people living in the life after this life. The title is Lessons Gathered From Every Season of Your Existence: Shared by Voices Dwelling Beyond the Veil. Author is T. Wesley Prandt. Book size is 6 by 9.

Target Market(s)

General

Font styles to use
Serif

```html
<!DOCTYPE html>
<html lang="en">
<head>
<meta charset="utf-8">
<title>Lanterns Along the Quiet Shore of Being — Cover</title>
<link href="https://fonts.googleapis.com/css2?family=Bree+Serif&display=swap" rel="stylesheet">
<style>
  :root {
    --sky-top: #a9cde9;
    --sky-mist: #6fa3d4;
    --sea-upper: #2f6fb4;
    --sea-mid: #174f8f;
    --sea-deep: #0c2f5c;
    --sea-floor: #071a38;
    --title-yellow: #ffe426;
    --text-white: #ffffff;
  }
  * { margin: 0; padding: 0; box-sizing: border-box; }
  html, body { width: 800px; height: 1200px; overflow: hidden; }
  body { font-family: "Bree Serif", Georgia, serif; }
  .cover {
    position: relative;
    width: 800px;
    height: 1200px;
    overflow: hidden;
  }
  .cover-backdrop {
    position: absolute;
    inset: 0;
    background: linear-gradient(180deg,
      var(--sky-top) 0%,
      var(--sky-mist) 18%,
      var(--sea-upper) 30%,
      var(--sea-mid) 50%,
      var(--sea-deep) 75%,
      var(--sea-floor) 100%);
  }
  .cover-text {
    position: absolute;
    left: 60px;
    right: 60px;
    top: 208px;
    text-align: center;
  }
  .book-title {
    color: var(--title-yellow);
    font-size: 58px;
    line-height: 78px;
    font-weight: 400;
    letter-spacing: 0.5px;
  }
  .book-subtitle {
    margin-top: 22px;
    color: var(--text-white);
    font-size: 44px;
    line-height: 58px;
    font-weight: 400;
    letter-spacing: 2px;
  }
  .book-author {
    position: absolute;
    left: 0;
    right: 0;
    top: 1052px;
    text-align: center;
    color: var(--text-white);
    font-size: 19px;
    letter-spacing: 10px;
    text-transform: uppercase;
  }
</style>
</head>
<body>
  <main class="cover">
    <div class="cover-backdrop" role="img" aria-label="Photograph of a calm open sea fading into misty blue sky"></div>
    <div class="cover-text">
      <h1 class="book-title">Lessons Gathered From Every Season of Your Existence</h1>
      <p class="book-subtitle">Shared by Voices Dwelling Beyond the Veil</p>
    </div>
    <p class="book-author">T. Wesley Prandt</p>
  </main>
</body>
</html>
```